QELVORN Sponsorship Template Deck for Annual Meeting

Need a template deck to highlight sponsors and exhibitors for an annual meeting. Most of the content will be company logos with limited text. Looking for interesting creative backgrounds. Need to incorporate the colors and logo for the meeting that have been uploaded. As well as the QELVORN company logo. QELVORN is a professional association for energy storage. here is a link to the meeting website https://ymr.qelvorn-example.org/
Need 4 Major sponsor slides:
Terawatt
Gigawatt
Megawatt
Kilowatt
The a different look for all other sponsors.
Font styles to use
Requirements
Must have
- at least 6 different looking slide templates

```html
<!DOCTYPE html>
<html lang="en">
<head>
<meta charset="utf-8">
<title>QELVORN 2024 Sponsorship Deck</title>
<link rel="stylesheet" href="https://fonts.googleapis.com/css2?family=Exo+2:wght@300;400;700;800&family=Hind:wght@400;600;700&display=swap">
<style>
:root{
  --board:#8f8d8e;
  --pill:#0a86db;
  --pill-text:#ffffff;
  --navy:#0a0f5c;
  --deep:#071b3d;
  --royal:#1b2fa8;
  --sky:#35b5ee;
  --label:#1a8fd8;
  --ink:#2a2f3a;
  --white:#ffffff;
}
*{margin:0;padding:0;box-sizing:border-box}
html,body{width:1200px;height:1047px;overflow:hidden;background:var(--board)}
.board{position:relative;width:1200px;height:1047px}
.slide{position:absolute;width:505px;height:284px;overflow:hidden}
.bg{position:absolute;inset:0}
.pill{position:absolute;border-radius:17px;background:var(--pill);color:var(--pill-text);
  font-family:"Exo 2",sans-serif;font-weight:800;display:flex;align-items:center;justify-content:center;letter-spacing:.5px}
.event-mark{position:absolute;font-family:"Exo 2",sans-serif;font-weight:800;color:var(--sky);
  font-size:11px;line-height:1;white-space:nowrap}
.page-no{position:absolute;width:16px;height:16px;border-radius:50%;background:var(--pill);color:#fff;
  font-family:"Hind",sans-serif;font-weight:700;font-size:6.5px;display:flex;align-items:center;justify-content:center;left:481px;top:260px}
.perks{position:absolute;list-style:none;font-family:"Hind",sans-serif;font-size:5.3px;line-height:11.7px}
.perks li{position:relative;padding-left:16px}
.perks li::before{content:"";position:absolute;left:0;top:4.5px;width:3px;height:3px;border-radius:50%;background:var(--pill)}
.tier-label{position:absolute;font-family:"Exo 2",sans-serif;font-weight:400;font-size:10px;color:var(--label);white-space:nowrap}
.logo-box{position:absolute;width:82px;height:47px;background:var(--white);display:flex;align-items:center;justify-content:center;
  font-family:"Hind",sans-serif;font-weight:600;text-align:center;line-height:1.05;box-shadow:0 1px 3px rgba(0,0,0,.12)}

/* cover */
.cover .bg{background:radial-gradient(ellipse at 60% 70%,#1e5fb8 0%,#0b1a78 40%,var(--navy) 75%)}
.cover .event-mark{left:0;right:0;text-align:center;top:45px;font-size:26px}
.cover .venue{position:absolute;left:0;right:0;top:78px;text-align:center;font-family:"Exo 2",sans-serif;font-size:4.5px;letter-spacing:1px;color:var(--sky)}
.cover .title{position:absolute;left:0;right:0;text-align:center;top:106px;font-family:"Exo 2",sans-serif;font-weight:800;color:#fff;font-size:28px;line-height:1}
.cover .pill{left:100px;top:141px;width:305px;height:34px;font-size:26px}

/* terawatt */
.terawatt .bg{background:radial-gradient(circle at 73% 50%,#2c8be0 0%,#0d4d9c 38%,#072a5c 75%)}
.terawatt .card{position:absolute;left:19px;top:55px;width:237px;height:190px;background:#fff;border:1.5px solid var(--pill)}
.terawatt .pill{left:39px;top:39px;width:198px;height:34px;font-size:26px}
.terawatt .perks{left:37px;top:92px;color:#555}
.terawatt .tier-label{left:37px;top:163px;color:var(--ink)}
.terawatt .logo-box{left:37px;top:186px;width:79px;height:44px;background:#e07070;color:#fff;font-size:7px;box-shadow:none}
.terawatt .sphere{position:absolute;left:294px;top:62px;width:158px;height:158px;border-radius:50%;
  background:radial-gradient(circle at 45% 40%,#ffffff 0%,#f0f4f8 55%,#b9c6d6 100%)}
.terawatt .sphere .event-mark{left:0;right:0;text-align:center;top:72px;font-size:11px}

/* gigawatt */
.gigawatt .bg{background:radial-gradient(ellipse at 40% 50%,#2340c8 0%,var(--royal) 50%,#13207e 100%)}
.gigawatt .event-mark{left:411px;top:22px}
.gigawatt .pill{left:157px;top:68px;width:197px;height:34px;font-size:26px}
.gigawatt .perks{left:97px;top:123px;color:#fff}
.gigawatt .tier-label{left:334px;top:117px;color:var(--sky)}
.gigawatt .logo-box{left:333px;top:144px;color:#222;font-size:13px}

/* megawatt */
.megawatt .bg{background:linear-gradient(90deg,#e9ecf0 0%,#f6f7f9 60%,#eceef1 100%)}
.megawatt .hex-art{position:absolute;left:0;top:0;width:215px;height:284px;
  background:linear-gradient(90deg,#0c5ca3 0%,#1a88cf 55%,rgba(233,236,240,0) 100%)}
.megawatt .event-mark{left:410px;top:22px}
.megawatt .pill{left:182px;top:33px;width:197px;height:34px;font-size:26px}
.megawatt .perks{left:183px;top:80px;color:#333}
.megawatt .tier-label{left:180px;top:167px}
.megawatt .logo-box.first{left:180px;top:188px;color:#0a4f8a;font-size:12px}
.megawatt .logo-box.second{left:269px;top:188px;color:#444;font-size:9px}

/* kilowatt */
.kilowatt .bg{background:radial-gradient(ellipse at 50% 45%,#ffffff 0%,#eef0f3 60%,#d9dde4 100%)}
.kilowatt .corner{position:absolute;width:60px;height:70px;background:linear-gradient(135deg,#1a4ea0,#6a86c8)}
.kilowatt .corner.tl{left:0;top:0;clip-path:polygon(0 0,100% 0,0 100%)}
.kilowatt .corner.tr{right:0;top:0;clip-path:polygon(0 0,100% 0,100% 100%)}
.kilowatt .corner.bl{left:0;bottom:0;clip-path:polygon(0 0,100% 100%,0 100%)}
.kilowatt .corner.br{right:0;bottom:0;clip-path:polygon(100% 0,100% 100%,0 100%)}
.kilowatt .event-mark{left:410px;top:22px}
.kilowatt .pill{left:47px;top:77px;width:197px;height:33px;font-size:26px}
.kilowatt .perks{left:54px;top:121px;color:#333}
.kilowatt .tier-label{left:307px;top:74px}
.kilowatt .logo-box.a{left:306px;top:96px;color:#1c3d6e;font-size:8px}
.kilowatt .logo-box.b{left:395px;top:96px;color:#3a4a5a;font-size:10px}
.kilowatt .logo-box.c{left:306px;top:150px;color:#1c4f9e;font-size:6.5px}

/* other sponsors */
.others .bg{background:radial-gradient(ellipse at 50% 50%,#0e3766 0%,#0a2448 55%,var(--deep) 100%)}
.others .pill{left:31px;top:20px;width:315px;height:33px;font-size:26px}
.others .event-mark{left:410px;top:28px}
.sponsor-grid{position:absolute;left:40px;top:77px;display:grid;grid-template-columns:repeat(6,63px);grid-auto-rows:36px;column-gap:9.2px;row-gap:9px}
.sponsor-grid .logo-box{position:static;width:63px;height:36px;font-size:6.5px;padding:2px;box-shadow:none}
.c-blue{color:#1a4f9e}.c-navy{color:#1b2a55}.c-teal{color:#0f8a8a}.c-red{color:#cc1f2a}.c-dark{color:#222}.c-green{color:#1e7a3c}
</style>
</head>
<body>
<main class="board">

  <section class="slide cover" style="left:75px;top:77px">
    <div class="bg" role="img" aria-label="Glowing blue particle wave background"></div>
    <div class="event-mark">QELVORN 2024</div>
    <div class="venue">HARBOR CREST RESORT AND SPA</div>
    <h1 class="title">QELVORN 2024</h1>
    <div class="pill">BUILDING CAPACITY</div>
    <div class="page-no">01</div>
  </section>

  <section class="slide megawatt" style="left:620px;top:77px">
    <div class="bg"></div>
    <div class="hex-art" role="img" aria-label="Blue hexagonal circuit pattern"></div>
    <div class="event-mark">QELVORN 2024</div>
    <h2 class="pill">MEGAWATT</h2>
    <ul class="perks">
      <li>Two (2) complimentary passes to the Annual Conference (valued at over $5,000).</li>
      <li>One (1) standard featured space in the Battery Products Expo.</li>
      <li>Opportunity to sponsor one networking break.</li>
      <li>Your logo will appear prominently on the conference website as Megawatt Conference Sponsor with a<br>direct link to your home page.</li>
      <li>Your logo will appear prominently on conference signage</li>
    </ul>
    <div class="tier-label">Megawatt Sponsors</div>
    <div class="logo-box first">Ferrolyn</div>
    <div class="logo-box second">Corvane Cycle</div>
    <div class="page-no">04</div>
  </section>

  <section class="slide terawatt" style="left:96px;top:381px">
    <div class="bg" role="img" aria-label="Blue digital circuit board background"></div>
    <div class="sphere" role="img" aria-label="Glowing white sphere with binary digits">
      <div class="event-mark">QELVORN 2024</div>
    </div>
    <div class="card"></div>
    <h2 class="pill">TERAWATT</h2>
    <ul class="perks">
      <li>Four (4) complimentary passes to the Annual Conference (valued at over $10,000).</li>
      <li>One (1) standard featured space in the Battery Products Expo.</li>
      <li>Opportunity to give conference welcome</li>
      <li>Sponsorship of the Opening Reception immediately prior to the dinner on<br>Day 1 of the conference.</li>
    </ul>
    <div class="tier-label">Terawatt Sponsor</div>
    <div class="logo-box">Sixteen Vale</div>
    <div class="page-no">02</div>
  </section>

  <section class="slide kilowatt" style="left:620px;top:381px">
    <div class="bg" role="img" aria-label="Light abstract tech background with blue hexagon corners"></div>
    <div class="corner tl"></div><div class="corner tr"></div><div class="corner bl"></div><div class="corner br"></div>
    <div class="event-mark">QELVORN 2024</div>
    <h2 class="pill">KILOWATT</h2>
    <ul class="perks">
      <li>One (1) complimentary pass to the Annual Conference (valued at over $2,000).</li>
      <li>One (1) standard featured space in the Battery Products Expo.</li>
      <li>Your logo will appear prominently on the conference website as Kilowatt Conference<br>Sponsor with a direct link to your home page.</li>
      <li>Your logo will appear prominently on conference signage.</li>
    </ul>
    <div class="tier-label">Megawatt Sponsors</div>
    <div class="logo-box a">BREVIK POWER</div>
    <div class="logo-box b">Tessmar</div>
    <div class="logo-box c">LUNDQVIST OHM</div>
    <div class="page-no">05</div>
  </section>

  <section class="slide gigawatt" style="left:96px;top:686px">
    <div class="bg" role="img" aria-label="Electric blue lightning background"></div>
    <div class="event-mark">QELVORN 2024</div>
    <h2 class="pill">GIGAWATT</h2>
    <ul class="perks">
      <li>Three (3) complimentary passes to the Annual Conference (valued at over $8,000).</li>
      <li>One (1) standard featured space in the Battery Products Expo.</li>
      <li>Opportunity to sponsor one event.</li>
      <li>Your logo will appear prominently displayed with full-color floor or window cling</li>
      <li>Your logo will appear prominently on the conference website as Gigawatt<br>Conference Sponsor with a direct link to your home page.</li>
    </ul>
    <div class="tier-label">Gigawatt Sponsor</div>
    <div class="logo-box">Voltara</div>
    <div class="page-no">03</div>
  </section>

  <section class="slide others" style="left:620px;top:686px">
    <div class="bg" role="img" aria-label="Dark navy circuit board background"></div>
    <h2 class="pill">OTHER SPONSORS</h2>
    <div class="event-mark">QELVORN 2024</div>
    <div class="sponsor-grid">
      <div class="logo-box c-blue">Norvia Cells</div>
      <div class="logo-box c-navy">KESTREL MATTER</div>
      <div class="logo-box c-navy" style="font-size:10px">Ulden</div>
      <div class="logo-box c-blue">Azure Pact</div>
      <div class="logo-box c-dark">Q&amp;R Hiring</div>
      <div class="logo-box c-dark" style="font-size:8px">Tellura</div>
      <div class="logo-box c-dark">Hargrove Law</div>
      <div class="logo-box c-navy">Decimo Works</div>
      <div class="logo-box c-navy" style="font-size:9px">Solvix</div>
      <div class="logo-box c-dark">FALCONRIDGE</div>
      <div class="logo-box c-dark">Brandt Flow</div>
      <div class="logo-box c-teal" style="font-size:8px">ARVENSEN</div>
      <div class="logo-box c-dark">Tradeline</div>
      <div class="logo-box c-red">KAZEMO</div>
      <div class="logo-box c-red" style="font-size:8px">Ashwood</div>
      <div class="logo-box c-blue">TESTMARK</div>
      <div class="logo-box c-dark">Nova Cell Materials</div>
      <div class="logo-box c-navy">Innova Grid</div>
      <div class="logo-box c-dark" style="font-size:9px">Quorix</div>
      <div class="logo-box c-green">Rewatt</div>
      <div class="logo-box c-dark">ATLASGRID</div>
      <div class="logo-box c-blue">Motive Society</div>
      <div class="logo-box c-dark">Tagwright</div>
      <div class="logo-box c-red">Holmgard</div>
    </div>
    <div class="page-no">06</div>
  </section>

</main>
</body>
</html>
```